Local Flower Farm Needs Business Card Design

I need business cards designed for a flower farm based in Eudora, Kansas.
Business Info:
We are a local cut flower farm located in Eudora, Kansas, founded by Corinne Haldwick. What started as a passion for agriculture and search for more joy in daily life has blossomed into a small business dedicated to providing the community with beautiful, fresh, and sustainable flowers. We specialize in local, seasonal blooms, ensuring that every petal reflects the care and dedication we pour into our craft. Our mission is to deliver the highest quality flowers directly to our customers through local farmers markets and to florists who share our commitment to sustainability. Join us in celebrating the beauty of nature, one bloom at a time!
Contact Details:
Corinne Haldwick
Owner
Phone 913-555-0147
Facebook: Rosalind Thorpe Gardens
Instagram: @RosalindThorpeGardens
Website: RosalindThorpeGardens.example
Target Market(s)
Wholesale to Florists and Direct to Consumer via Farmers Market
Industry/Entity Type
Florist, Farm
Contact Information for Business Card
Name, Contact Info, Logo
Look and feel
Each slider illustrates characteristics of the customer's brand and the style your logo design should communicate.

```html
<!DOCTYPE html>
<html lang="en">
<head>
<meta charset="utf-8">
<title>Rosalind Thorpe Gardens – Business Card</title>
<link rel="stylesheet" href="https://fonts.googleapis.com/css2?family=Bodoni+Moda:wght@500&family=Nunito:wght@400;500&display=swap">
<style>
  :root {
    --backdrop: #2b2b2c;
    --card-white: #ffffff;
    --forest: #3d5527;
    --ink: #1d2e29;
    --muted: #6b6f6c;
    --rule: #b9bcba;
  }
  * { box-sizing: border-box; margin: 0; padding: 0; }
  html, body { width: 1200px; height: 1195px; overflow: hidden; }
  body {
    background: var(--backdrop);
    position: relative;
    font-family: "Nunito", sans-serif;
  }
  .card {
    position: absolute;
    top: 232px;
    width: 420px;
    height: 730px;
    border-radius: 30px;
    display: flex;
    flex-direction: column;
    align-items: center;
  }
  .card--front { left: 150px; background: var(--card-white); color: var(--ink); }
  .card--back { left: 630px; background: var(--forest); color: var(--card-white); justify-content: center; }

  .brand-seal {
    width: 240px;
    height: 240px;
    border: 1.5px solid currentColor;
    border-radius: 50%;
    display: flex;
    align-items: center;
    justify-content: center;
    text-align: center;
    font-family: "Bodoni Moda", serif;
    font-weight: 500;
    font-size: 25px;
    line-height: 1.25;
    letter-spacing: 1.5px;
    text-transform: uppercase;
    padding: 20px;
  }
  .card--front .brand-seal { margin-top: 60px; }
  .card--back .brand-seal { width: 300px; height: 300px; font-size: 30px; }

  .holder-name {
    margin-top: 34px;
    font-family: "Bodoni Moda", serif;
    font-weight: 500;
    font-size: 27px;
    letter-spacing: 1px;
    text-transform: uppercase;
  }
  .holder-role { margin-top: 4px; font-size: 15px; color: var(--muted); }

  .divider {
    display: flex;
    align-items: center;
    gap: 8px;
    margin-top: 20px;
  }
  .divider::before, .divider::after {
    content: "";
    width: 70px;
    height: 1px;
    background: var(--rule);
  }
  .icon {
    width: 20px;
    height: 20px;
    border-radius: 4px;
    background: var(--ink);
    display: block;
  }
  .details {
    margin-top: 10px;
    text-align: center;
    font-size: 16px;
    line-height: 1.45;
    letter-spacing: 0.3px;
  }
</style>
</head>
<body>
  <section class="card card--front">
    <div class="brand-seal">Rosalind Thorpe Gardens</div>
    <h1 class="holder-name">Corinne Haldwick</h1>
    <p class="holder-role">Owner</p>

    <div class="divider">
      <svg class="icon" viewBox="0 0 20 20" aria-label="phone"><rect width="20" height="20" rx="4" fill="#1d2e29"/><path d="M6 5c1 0 1.5 2 1.5 2.5S6.5 8.5 7 9.5s2 2.5 3 3 1.5-1 2-1 2.5.5 2.5 1.5-1 1.5-2 1.5C8 14.5 5.5 12 5 8c0-1.5.5-3 1-3z" fill="#fff"/></svg>
      <svg class="icon" viewBox="0 0 20 20" aria-label="email"><rect width="20" height="20" rx="4" fill="#1d2e29"/><rect x="4.5" y="6" width="11" height="8" fill="none" stroke="#fff" stroke-width="1.3"/><path d="M4.5 6l5.5 4.5L15.5 6" fill="none" stroke="#fff" stroke-width="1.3"/></svg>
      <svg class="icon" viewBox="0 0 20 20" aria-label="website"><rect width="20" height="20" rx="4" fill="#1d2e29"/><circle cx="10" cy="10" r="5.5" fill="none" stroke="#fff" stroke-width="1.3"/><path d="M4.5 10h11M10 4.5c-2.5 3-2.5 8 0 11M10 4.5c2.5 3 2.5 8 0 11" fill="none" stroke="#fff" stroke-width="1"/></svg>
    </div>
    <p class="details">
      913-555-0147<br>
      RosalindThorpe@Gardens.example<br>
      www.RosalindThorpeGardens.example
    </p>

    <div class="divider">
      <span class="icon"></span>
      <span class="icon"></span>
    </div>
    <p class="details">
      Rosalind Thorpe Gardens<br>
      @RosalindThorpeGardens
    </p>
  </section>

  <section class="card card--back">
    <div class="brand-seal">Rosalind Thorpe Gardens</div>
  </section>
</body>
</html>
```